Honey jar label for small US farm

My daughters have 6 beehives and will be producing 300-400 jars of honey this season that they plan to sell at the farmers' market.
We are looking for a label design for small honey jars.
Label size:  1.5 inches high and 3 inches wide.
The label will be a simple RECTANGLE (no special cut)
We would like a playful look but upscale enough. We don't think that flowers or bees add anything. We like cleaner looks but not cold.
Maybe one could also represent the 3 sisters somewhere on the label. As elegant stick figures maybe?
One could also imagine a design where the label is black and the text/images are white to add some dramatic effect. The jar lid is black.
The honey is raw, un-pasturized, straight from the beehive.

Target Market(s)
Farm stand, sold by the 3 sisters who are 11, 9 and 6
Industry/Entity Type
Food Production
Colors
Designer to choose colors to be used in the design.
Requirements
Must have
- Name (means three sisters in English): Clos Vert
- What it is: Greenvale Raw Honey
- Net weight: 3.75oz (110ml)
- Location: Maplecroft, VT
- Text on one of the sides: Sister to sister we will always be, a couple of nuts off the family tree!
- Note that the jar is an hexagon. See the attached STOCK photo.
- Therefore, a little more than 1 inch is on the front facing, and 0.75 inches on each sides.

Nice to have
- The design should be elegant (but not ornate), but clean. Inviting and fun.
- No need for bees or flowers which would not make it look upscale.
- No gold or "over the top" fancy. Modern but not cold.
- Remember that this is a honey brand for 3 young sisters. Something playful but upscale would work too.
- Not sure about color codes. We are quite happy staying in grey scales, but a little bit of colour might work too.

Should not have
- No UPC code needed

```html
<!DOCTYPE html>
<html lang="en">
<head>
<meta charset="utf-8">
<title>Clos Vert – Greenvale Raw Honey Label</title>
<link rel="stylesheet" href="https://fonts.googleapis.com/css2?family=Oswald:wght@500;600&family=Arimo:wght@400;700&display=swap">
<style>
  :root {
    --page: #ffffff;
    --label-dark: #2e2e2e;
    --label-mid: #4a4a4a;
    --label-glow: #8d8d8d;
    --fold-line: #6a6a6a;
    --frame: #1c1c1c;
    --honey: #ffd21a;
    --ink-light: #ffffff;
  }
  html, body {
    margin: 0;
    width: 1200px;
    height: 647px;
    overflow: hidden;
    background: var(--page);
  }
  .canvas {
    position: relative;
    width: 1200px;
    height: 647px;
  }
  .label {
    position: absolute;
    left: 50px;
    top: 48px;
    width: 1082px;
    height: 542px;
    box-sizing: border-box;
    border: 2px solid var(--frame);
    background:
      radial-gradient(ellipse 300px 260px at 542px 215px, var(--label-glow) 0%, var(--label-mid) 55%, transparent 100%),
      linear-gradient(90deg, var(--label-dark) 0%, var(--label-mid) 50%, var(--label-dark) 100%);
  }
  .fold {
    position: absolute;
    top: 0;
    bottom: 0;
    width: 0;
    border-left: 1px solid var(--fold-line);
  }
  .fold--left { left: 271px; }
  .fold--right { left: 811px; }

  .side-verse {
    position: absolute;
    left: 0;
    width: 271px;
    top: 92px;
    margin: 0;
    text-align: center;
    font-family: "Arimo", Arial, sans-serif;
    font-size: 23px;
    line-height: 28px;
    color: var(--ink-light);
  }
  .brand-name {
    position: absolute;
    left: 271px;
    width: 540px;
    top: 88px;
    margin: 0;
    text-align: center;
    font-family: "Oswald", "Arial Narrow", sans-serif;
    font-weight: 600;
    font-size: 66px;
    line-height: 72px;
    letter-spacing: 4px;
    text-transform: uppercase;
    color: var(--honey);
  }
  .product-name {
    position: absolute;
    left: 271px;
    width: 540px;
    top: 276px;
    margin: 0;
    text-align: center;
    font-family: "Oswald", "Arial Narrow", sans-serif;
    font-weight: 500;
    font-size: 36px;
    line-height: 44px;
    letter-spacing: 2px;
    color: var(--ink-light);
  }
  .sisters-art {
    position: absolute;
    left: 394px;
    top: 330px;
    width: 294px;
    height: 110px;
    border-radius: 8px;
    background: radial-gradient(ellipse at center, rgba(255,255,255,0.18), rgba(255,255,255,0.04));
  }
  .ground-arc {
    position: absolute;
    left: 352px;
    top: 432px;
    width: 384px;
    height: 50px;
  }
  .net-weight, .origin {
    position: absolute;
    top: 496px;
    margin: 0;
    text-align: center;
    font-family: "Arimo", Arial, sans-serif;
    font-weight: 700;
    font-size: 22px;
    line-height: 28px;
    color: var(--ink-light);
  }
  .net-weight { left: 271px; width: 540px; }
  .origin { left: 811px; width: 269px; }
</style>
</head>
<body>
<div class="canvas">
  <section class="label" aria-label="Honey jar label">
    <div class="fold fold--left"></div>
    <div class="fold fold--right"></div>

    <p class="side-verse">Sister to sister<br>we will always be,<br>a couple of nuts<br>off the family tree!</p>

    <h1 class="brand-name">Clos<br>Vert</h1>
    <h2 class="product-name">GREENVALE RAW HONEY</h2>

    <div class="sisters-art" role="img" aria-label="Line drawing of three little sisters dancing"></div>
    <svg class="ground-arc" viewBox="0 0 384 50" aria-hidden="true">
      <path d="M0 46 Q192 -18 384 46 Q192 6 0 46 Z" fill="var(--honey)"/>
    </svg>

    <p class="net-weight">3.75oz (110ml)</p>
    <p class="origin">Maplecroft, VT</p>
  </section>
</div>
</body>
</html>
```